Business Card for a mobile physiotherapy company

I need a layout for a business card for a mobile physiotherapy company.
Slogan is "Mobile Physiotherapy - Your Road To Recovery"
Phone number is 867-555-0142
Email VardenTherapy@postnest.ca (subject to change with website)
Website www.VardenTherapy.ca
My name and credentials: Luke Varden Luke Varden, BSc(kin), MPT, CAFCI, IMS
Information maybe included: Direct Billing, Services including Physiotherapy, IMS, acupuncture
Maybe include facebook and instagram logos
One side with the logo clean and sharp
Other side with details, try not to look too busy, keep everything concise

```html
<!DOCTYPE html>
<html lang="en">
<head>
<meta charset="utf-8">
<title>Varden Therapy Business Card</title>
<link rel="stylesheet" href="https://fonts.googleapis.com/css2?family=Bebas+Neue&family=Lato:ital,wght@0,400;0,700;1,400;1,700&display=swap">
<style>
  :root {
    --navy: #1f3c6c;
    --navy-deep: #183361;
    --navy-light: #2c5084;
    --green: #0f5a4a;
    --paper: #f4f4f4;
    --grey-text: #6b6b6b;
    --stage: #e6e6e6;
    --white: #ffffff;
  }
  html, body {
    margin: 0;
    padding: 0;
    width: 1200px;
    height: 960px;
    overflow: hidden;
    background: var(--stage);
    font-family: "Lato", Arial, sans-serif;
  }
  .canvas {
    position: relative;
    width: 1200px;
    height: 960px;
  }
  .card {
    position: absolute;
    left: 295px;
    width: 615px;
    height: 352px;
    overflow: hidden;
  }
  /* Front */
  .card-front {
    top: 103px;
    background: linear-gradient(135deg, var(--navy-deep) 0%, var(--navy) 55%, var(--navy-light) 100%);
  }
  .brand {
    position: absolute;
    left: 0;
    right: 0;
    top: 190px;
    text-align: center;
    color: var(--white);
    font-weight: 700;
  }
  .brand-name {
    display: block;
    font-size: 54px;
    letter-spacing: 4px;
    line-height: 1;
  }
  .brand-sub {
    display: block;
    margin-top: 14px;
    font-size: 22px;
    letter-spacing: 9px;
    line-height: 1;
  }
  /* Back */
  .card-back {
    top: 508px;
    background: var(--paper);
  }
  .person {
    position: absolute;
    left: 0;
    right: 0;
    top: 96px;
    text-align: center;
  }
  .person-name {
    margin: 0;
    font-family: "Bebas Neue", Impact, sans-serif;
    font-weight: 400;
    font-size: 31px;
    line-height: 1;
    color: var(--navy);
    letter-spacing: 0.5px;
  }
  .person-credentials {
    margin: 3px 0 0;
    font-size: 14px;
    color: var(--grey-text);
  }
  .services {
    position: absolute;
    right: 344px;
    top: 203px;
    margin: 0;
    padding: 0;
    list-style: none;
    text-align: right;
    font-size: 14px;
    line-height: 18px;
    color: var(--grey-text);
  }
  .bullet {
    display: inline-block;
    width: 5px;
    height: 5px;
    border-radius: 50%;
    background: var(--navy);
    vertical-align: middle;
    margin: 0 2px 2px 4px;
  }
  .divider {
    position: absolute;
    left: 306px;
    top: 194px;
    width: 2px;
    height: 74px;
    background: var(--navy);
  }
  .contact {
    position: absolute;
    left: 341px;
    top: 195px;
    margin: 0;
    padding: 0;
    list-style: none;
    font-size: 14px;
    line-height: 18px;
    color: var(--grey-text);
  }
  .contact li {
    display: flex;
    align-items: center;
  }
  .contact-icon {
    width: 11px;
    height: 11px;
    margin-right: 8px;
    flex: none;
  }
  .social-dot {
    width: 9px;
    height: 9px;
    border-radius: 50%;
    background: var(--navy-deep);
    margin: 0 8px 0 1px;
    flex: none;
  }
  .footer-band {
    position: absolute;
    left: 0;
    bottom: 0;
    width: 615px;
    height: 62px;
  }
  .slogan {
    position: absolute;
    left: 0;
    right: 0;
    bottom: 6px;
    margin: 0;
    text-align: center;
    font-size: 13px;
    font-style: italic;
    color: var(--white);
  }
  .slogan strong {
    font-weight: 700;
  }
</style>
</head>
<body>
<div class="canvas">

  <section class="card card-front">
    <div class="brand">
      <span class="brand-name">VARDEN</span>
      <span class="brand-sub">THERAPY</span>
    </div>
  </section>

  <section class="card card-back">
    <div class="person">
      <h1 class="person-name">Luke Varden Luke Varden</h1>
      <p class="person-credentials">BSc (kin), MPT, CAFCI, IMS</p>
    </div>

    <ul class="services">
      <li>Direct Billing<span class="bullet"></span></li>
      <li>Services including Physiotherapy<span class="bullet"></span></li>
      <li>IMS<span class="bullet"></span> Acupuncture<span class="bullet"></span></li>
    </ul>

    <div class="divider"></div>

    <ul class="contact">
      <li>
        <svg class="contact-icon" viewBox="0 0 12 12" aria-hidden="true">
          <path d="M2.5 1 L4.5 1 L5.2 3.6 L4 4.6 Q5 7 7.4 8 L8.4 6.8 L11 7.5 L11 9.5 Q10.5 11 9 11 Q1 10 1 3 Q1 1.5 2.5 1 Z" fill="var(--navy)"/>
        </svg>867-555-0142
      </li>
      <li>
        <svg class="contact-icon" viewBox="0 0 12 12" aria-hidden="true">
          <rect x="1" y="2.5" width="10" height="7" fill="none" stroke="var(--navy)" stroke-width="1.2"/>
          <path d="M1 2.5 L6 6.5 L11 2.5" fill="none" stroke="var(--navy)" stroke-width="1.2"/>
        </svg>VardenTherapy@postnest.ca
      </li>
      <li>
        <svg class="contact-icon" viewBox="0 0 12 12" aria-hidden="true">
          <circle cx="6" cy="6" r="5" fill="none" stroke="var(--navy)" stroke-width="1.1"/>
          <ellipse cx="6" cy="6" rx="2.2" ry="5" fill="none" stroke="var(--navy)" stroke-width="1"/>
          <path d="M1 6 H11 M2 3.5 H10 M2 8.5 H10" stroke="var(--navy)" stroke-width="0.9"/>
        </svg>www.VardenTherapy.ca
      </li>
      <li><span class="social-dot"></span>VardenTherapy</li>
    </ul>

    <svg class="footer-band" viewBox="0 0 615 62" aria-hidden="true">
      <path d="M0 0 Q307 38 615 0 L615 12 Q307 40 0 12 Z" fill="var(--green)"/>
      <path d="M0 14 Q307 44 615 14 L615 62 L0 62 Z" fill="var(--navy)"/>
    </svg>
    <p class="slogan"><strong>Mobile Physiotherapy</strong> - Your Road To Recovery</p>
  </section>

</div>
</body>
</html>
```